Business card for Eyelash extension salon in Beverly Hills,California USA

We need new business card for our salon in Beverly Hills. The salon name is 'Lashvera' . We would like to have...Business name: Lashvera Name of person: will provide later Address 4720 N.Alder Crest Ave Beverly Hills , CA 90210 Phone: will provide later (Text only) Web: www.lashverastudio.example Snapgrid icon, Circlebook icon follow us for seasonal campaign and news @lashverastudiolounge Design should look elegant, high-end, clean, simple, cohesive with my brand. Please refer my brand board. Business name color will be metallic bronzy color. Im thinking grey background or white background. Thanks

Target Market(s)

25-35. Gender neutral. People who are in Entertainment business industry.
This is High-end Eyelash extension salon in Beverly Hills

Industry/Entity Type

Beauty Salon

Contact Information for Business Card

Business name: Lashvera
Name of person: will provide later
Address 4720 N.Alder Crest Ave Beverly Hills , CA 90210
Phone: will provide later (Text only)
Web: www.lashverastudio.example
Snapgrid icon, Circlebook icon
follow us for seasonal campaign and news @lashverastudiolounge

Requirements
Must have
• Beautiful, elegant, clean and simple look but very attractive and modern
Should not have
• We don't like too clutter, too busy designs.

```html
<!DOCTYPE html>
<html lang="en">
<head>
<meta charset="utf-8">
<title>Lashvera Business Card</title>
<link href="https://fonts.googleapis.com/css2?family=Cormorant+Garamond:wght@400;600&family=Montserrat:wght@400&display=swap" rel="stylesheet">
<style>
  :root {
    --bronze: #8c6b55;
    --bronze-light: #a4826b;
    --paper: #ffffff;
    --backdrop: #e9e7e4;
    --ink-light: #f6efe9;
    --photo-top: #eef2f3;
    --photo-bottom: #c9d3cf;
  }
  * { box-sizing: border-box; margin: 0; padding: 0; }
  html, body { width: 1200px; height: 911px; overflow: hidden; }
  body {
    background: var(--backdrop);
    display: flex; align-items: center; justify-content: center; gap: 40px;
    font-family: "Cormorant Garamond", serif;
  }
  .card {
    position: relative; width: 540px; height: 309px;
    background: var(--paper);
    box-shadow: 0 6px 18px rgba(0,0,0,.12);
    overflow: hidden;
  }
  /* front */
  .info-panel {
    position: absolute; top: 0; left: 240px; width: 250px; height: 212px;
    background: linear-gradient(135deg, var(--bronze-light), var(--bronze));
    color: var(--ink-light);
    padding: 22px 18px 16px 24px;
  }
  .person-name { font-size: 19px; font-weight: 600; letter-spacing: .04em; text-transform: uppercase; line-height: 1.2; }
  .person-title { font-size: 12px; letter-spacing: .05em; text-transform: uppercase; line-height: 1.3; margin-bottom: 10px; }
  .address { font-size: 12px; line-height: 1.35; margin-bottom: 10px; }
  .contact-list { list-style: none; font-size: 11.5px; line-height: 1.55; }
  .contact-list li { display: flex; align-items: center; gap: 7px; white-space: nowrap; }
  .contact-list svg { width: 10px; height: 10px; flex: none; }
  .brand {
    position: absolute; left: 40px; bottom: 44px;
    color: var(--bronze);
  }
  .brand-name { font-size: 52px; font-weight: 400; line-height: 1; letter-spacing: .01em; }
  .brand-place {
    font-family: "Montserrat", sans-serif; font-size: 8px; letter-spacing: .3em;
    text-transform: uppercase; margin-top: 6px; padding-left: 96px;
  }
  /* back */
  .card-back { padding: 12px; }
  .photo-area {
    position: absolute; top: 12px; left: 12px; width: 398px; height: 285px;
    background: linear-gradient(160deg, var(--photo-top), var(--photo-bottom));
  }
  .side-band {
    position: absolute; top: 12px; right: 12px; width: 118px; height: 285px;
    background: var(--bronze);
    color: var(--ink-light);
    display: flex; flex-direction: column; justify-content: space-between; align-items: center;
    padding: 18px 8px 16px;
  }
  .band-brand { font-size: 20px; }
  .social-list { list-style: none; font-size: 11px; display: flex; flex-direction: column; gap: 6px; align-items: flex-start; }
  .social-list li { display: flex; align-items: center; gap: 6px; }
  .social-dot { width: 10px; height: 10px; border-radius: 50%; background: var(--paper); }
</style>
</head>
<body>
  <article class="card card-front">
    <div class="brand">
      <div class="brand-name">Lashvera</div>
      <div class="brand-place">Beverly Hills</div>
    </div>
    <section class="info-panel">
      <div class="person-name">Dana Whitlow</div>
      <div class="person-title">CEO/Founder</div>
      <p class="address">4720 N.Alder Crest Ave<br>Beverly Hills<br>CA 90210</p>
      <ul class="contact-list">
        <li><svg viewBox="0 0 10 10"><path d="M2 1l2 2-1 1.2c.6 1.2 1.5 2.1 2.8 2.8L7 6l2 2-1.2 1.5C4.5 9 1 5.5.5 2.2z" fill="currentColor"/></svg>555 014 2290</li>
        <li><svg viewBox="0 0 10 10"><rect x=".5" y="2" width="9" height="6" fill="none" stroke="currentColor"/><path d="M.5 2l4.5 3.5L9.5 2" fill="none" stroke="currentColor"/></svg>news@lashverastudio.example</li>
        <li><svg viewBox="0 0 10 10"><circle cx="5" cy="5" r="4.3" fill="none" stroke="currentColor"/><path d="M.7 5h8.6M5 .7c-2 2.5-2 6.1 0 8.6M5 .7c2 2.5 2 6.1 0 8.6" fill="none" stroke="currentColor" stroke-width=".7"/></svg>www.lashverastudio.example</li>
      </ul>
    </section>
  </article>

  <article class="card card-back">
    <div class="photo-area" role="img" aria-label="Photo of macramé plant hangers with green trailing plants in front of a bright window"></div>
    <aside class="side-band">
      <div class="band-brand">Lashvera</div>
      <ul class="social-list">
        <li><span class="social-dot"></span>Circlebook</li>
        <li><span class="social-dot"></span>Snapgrid</li>
      </ul>
    </aside>
  </article>
</body>
</html>
```